we can communicate on this, but i want to follow the approach we took on Pellew|Marsh & Quinlan but i feel the card front needs the black background and the platinum and gold logo. The back? I am open. we can use the same info from PM&Q. Velmont Arc is an enhanced equity investment fund - basically a very exclusive boutique hedge fund that uses only stock options. very advanced things. hope you are interested

Contact Information for Business Card

Dr. Lewis T. Brennick, CFA
Scientifique de fusée financière
701.555.0143
LTBquant47@mailvantor.com

4718 Willow Creek Bend W.
West Fargo, ND 58078

No web site

Colors

Designer to choose colors to be used in the design.

Requirements
Nice to have
• I tend to prefer the most visible applications of the logo to include logo and name, the logo version with a black background and the gold and platinum components separated by the black. I see this working well for a single side (logo and name - this is card front to me).
• I am fairly open to other treatments on the reverse side with the data. To me, it makes sense to have a different color rendition of the logo on the reverse and it may be a muted black tone on tone or an oversized portion that would have spot UV. Or, the reverse may play with colors and layout
Should not have
• Other colors = no no
• Decorative font

```html
<!DOCTYPE html>
<html lang="en">
<head>
<meta charset="utf-8">
<title>Velmont Arc – Business Card</title>
<link rel="stylesheet" href="https://fonts.googleapis.com/css2?family=Montserrat:wght@400;500;700&display=swap">
<style>
  :root {
    --bg: #9c9c9c;
    --ink: #1a1a1a;
    --card-black: #262626;
    --paper: #ffffff;
    --gold: #c9a227;
  }
  * { box-sizing: border-box; margin: 0; padding: 0; }
  html, body {
    width: 1200px; height: 930px; overflow: hidden;
    background: var(--bg);
    font-family: "Montserrat", sans-serif;
  }
  .stage { position: relative; width: 1200px; height: 930px; }

  .card {
    position: absolute;
    width: 560px; height: 320px;
    border-radius: 22px;
    overflow: hidden;
  }

  /* Front */
  .card-front {
    left: 60px; top: 90px;
    background: var(--card-black);
    display: flex; align-items: center; justify-content: center;
  }
  .front-mark { display: flex; align-items: center; gap: 16px; }
  .mark-circle {
    width: 26px; height: 26px; border-radius: 50%;
    background: var(--gold);
  }
  .front-name {
    color: var(--gold);
    font-weight: 700; font-size: 40px; letter-spacing: 1px;
    text-transform: uppercase;
  }

  /* Back */
  .card-back {
    left: 580px; top: 520px;
    background: var(--paper);
    color: var(--ink);
  }
  .back-wave { position: absolute; inset: 0; width: 100%; height: 100%; }

  .back-brand {
    position: absolute; left: 30px; top: 112px;
    display: flex; align-items: center; gap: 10px;
  }
  .back-brand .mark-circle { width: 20px; height: 20px; }
  .back-brand-name {
    color: var(--ink);
    font-weight: 700; font-size: 26px; letter-spacing: 0.5px;
    text-transform: uppercase;
  }

  .person { position: absolute; right: 30px; top: 30px; text-align: right; }
  .person-name {
    color: var(--gold);
    font-weight: 500; font-size: 22px; letter-spacing: 0.5px;
    text-transform: uppercase;
  }
  .person-title { font-size: 14px; margin-top: 2px; }
  .rule-top {
    position: absolute; right: 28px; top: 90px;
    width: 300px; height: 1.5px; background: var(--gold);
  }

  .address {
    position: absolute; right: 30px; top: 102px;
    text-align: right; font-size: 14px; line-height: 1.45; font-style: normal;
  }

  .rule-bottom {
    position: absolute; left: 30px; top: 206px;
    width: 250px; height: 1.5px; background: var(--gold);
  }
  .contact {
    position: absolute; left: 30px; top: 218px;
    list-style: none; font-size: 14px; line-height: 1.6;
  }
  .contact li { display: flex; align-items: center; gap: 8px; }
  .contact svg { width: 11px; height: 11px; flex: none; }
</style>
</head>
<body>
<main class="stage">

  <section class="card card-front" aria-label="Card front">
    <div class="front-mark">
      <span class="mark-circle"></span>
      <span class="front-name">Velmont Arc</span>
    </div>
  </section>

  <section class="card card-back" aria-label="Card back">
    <svg class="back-wave" viewBox="0 0 560 320" preserveAspectRatio="none" aria-hidden="true">
      <path d="M560 172 C480 172 440 222 380 262 C320 300 210 308 0 314 L0 320 L560 320 Z" fill="var(--card-black)"/>
      <path d="M560 165 C478 165 436 215 376 255 C316 293 206 302 0 308" fill="none" stroke="var(--gold)" stroke-width="4"/>
    </svg>

    <div class="back-brand">
      <span class="mark-circle"></span>
      <span class="back-brand-name">Velmont Arc</span>
    </div>

    <div class="person">
      <div class="person-name">Dorian Kessel</div>
      <div class="person-title">President</div>
    </div>
    <div class="rule-top"></div>

    <address class="address">
      2817 Halden Street<br>
      Brookvale, MO 63190
    </address>

    <div class="rule-bottom"></div>
    <ul class="contact">
      <li>
        <svg viewBox="0 0 12 12" aria-hidden="true"><path d="M2.5 1 L4.5 1 L5.2 3.4 L4 4.4 C4.6 5.8 6.2 7.4 7.6 8 L8.6 6.8 L11 7.5 L11 9.5 C11 10.4 10.3 11 9.5 11 C5 11 1 7 1 2.5 C1 1.7 1.6 1 2.5 1 Z" fill="var(--gold)"/></svg>
        469-555-0192
      </li>
      <li>
        <svg viewBox="0 0 12 12" aria-hidden="true"><rect x="1" y="2.5" width="10" height="7" fill="none" stroke="var(--gold)" stroke-width="1.3"/><path d="M1 2.5 L6 6.5 L11 2.5" fill="none" stroke="var(--gold)" stroke-width="1.3"/></svg>
        info@velmontarc.com
      </li>
    </ul>
  </section>

</main>
</body>
</html>
```